Risk Management Company in need of Business Card Design

We sell risk management insurance to Lenders (Banks, Credit Unions, Real Estate Trust).

We need a very clean, professional card that will leave a great impression.

We are looking to use a blue color for our logo on the card (Preferably close to royal blue but are open to looking at navy blue or any darker blues as well).

Please see the logo attached to get an idea. We are open to writing Harbor Ledger Under the logo or next to the logo. Really whatever looks best.

Target Market(s)

Banks, Credit Unions, Real Estate Trusts

Industry/Entity Type

Insurance

Contact Information for Business Card

Name: Tom Brandish
Title: Regional Sales Director
Email: tbrandish@harborledger-example.net
C:410-555-0137
D:410-555-0182
888-555-0149 Ext.318
F:443-555-0164 (We would like to see some cards without the fax number as well to compare)

Company Name: Harbor Ledger
Website: www.harborledger-example.net

Address: 718 E. Marlow St. Suite 340, Fenwick, OR 21287 (Preferably written on the bottom of the card in small print.)

Colors
0355a3
0455a3

Requirements
Nice to have
• We would like to see a couple of where the back has the logo in reverse colors (Logo White, Background Blue)

```html
<!DOCTYPE html>
<html lang="en">
<head>
<meta charset="utf-8">
<title>Harbor Ledger – Business Card</title>
<link rel="stylesheet" href="https://fonts.googleapis.com/css2?family=Cinzel:wght@500&family=PT+Sans:wght@400;700&display=swap">
<style>
  :root {
    --slate: #2f4e5d;
    --grey: #8a8c8e;
    --ink: #3a3a3a;
    --paper: #ffffff;
    --backdrop: #e9e7e4;
  }
  * { box-sizing: border-box; margin: 0; padding: 0; }
  html, body { width: 1200px; height: 505px; overflow: hidden; }
  body {
    background: var(--backdrop);
    font-family: "PT Sans", sans-serif;
    display: flex;
    align-items: center;
    justify-content: center;
    gap: 30px;
  }
  .card {
    position: relative;
    width: 560px;
    height: 320px;
    overflow: hidden;
    box-shadow: 0 6px 18px rgba(0,0,0,.25);
  }

  /* Front */
  .card-front { background: var(--paper); color: var(--ink); }
  .wordmark {
    position: absolute;
    top: 70px; left: 0; right: 0;
    display: flex; align-items: center; justify-content: center; gap: 14px;
  }
  .wordmark-square { width: 22px; height: 22px; background: var(--slate); }
  .wordmark-name {
    font-family: "Cinzel", serif;
    font-weight: 500;
    font-size: 30px;
    letter-spacing: 1px;
    color: var(--slate);
  }
  .person {
    position: absolute;
    top: 156px; right: 292px;
    text-align: right;
  }
  .person-name { font-weight: 700; font-size: 20px; }
  .person-title { font-size: 17px; margin-top: 2px; }
  .address { font-size: 15px; line-height: 1.25; margin-top: 22px; }
  .divider {
    position: absolute;
    top: 160px; left: 280px;
    width: 1px; height: 108px;
    background: #cfcfcf;
  }
  .contact-list {
    position: absolute;
    top: 152px; left: 292px;
    list-style: none;
    font-size: 14px;
  }
  .contact-list li { display: flex; align-items: center; gap: 8px; height: 23px; }
  .contact-list svg { width: 13px; height: 13px; fill: var(--ink); flex: none; }
  .ext { font-size: 10px; margin-left: 3px; }
  .footer-bands { position: absolute; bottom: 0; left: 0; width: 560px; height: 50px; }

  /* Back */
  .card-back {
    background: var(--slate);
    color: var(--paper);
    display: flex; flex-direction: column; align-items: center; justify-content: center;
  }
  .back-name {
    font-family: "Cinzel", serif;
    font-weight: 500;
    font-size: 46px;
    letter-spacing: 1px;
  }
  .back-url {
    font-weight: 700;
    font-size: 17px;
    letter-spacing: 3px;
    margin-top: 14px;
  }
</style>
</head>
<body>
  <section class="card card-front">
    <div class="wordmark">
      <span class="wordmark-square"></span>
      <span class="wordmark-name">Harbor Ledger</span>
    </div>

    <div class="person">
      <p class="person-name">Tom Brandish</p>
      <p class="person-title">Regional Sales Director</p>
      <p class="address">718 E. Marlow St.<br>Suite 340, Fenwick<br>OR 21287</p>
    </div>

    <span class="divider"></span>

    <ul class="contact-list">
      <li><svg viewBox="0 0 16 16"><path d="M3 1l3 3-2 2c1 2 3 4 5 5l2-2 3 3-2 3C6 14 2 10 1 3z"/></svg>410-555-0182</li>
      <li><svg viewBox="0 0 16 16"><path d="M3 1l3 3-2 2c1 2 3 4 5 5l2-2 3 3-2 3C6 14 2 10 1 3z"/></svg>888-555-0149<span class="ext">Ext.318</span></li>
      <li><svg viewBox="0 0 16 16"><path d="M4 1h6v4H4zM1 6h14v6h-3v3H4v-3H1zM5 10v4h6v-4z"/></svg>443-555-0164</li>
      <li><svg viewBox="0 0 16 16"><path d="M1 4h14v10H1zM2 5l6 5 6-5v1l-6 5-6-5z"/></svg>tbrandish@harborledger-example.net</li>
      <li><svg viewBox="0 0 16 16"><path d="M8 1a7 7 0 100 14A7 7 0 008 1zm0 1.5c.9 1.2 1.5 2.9 1.6 4.7H6.4C6.5 5.4 7.1 3.7 8 2.5zM2.6 8.8h2.3c.1 1.6.5 3 1.1 4.1A5.5 5.5 0 012.6 8.8zm0-1.6A5.5 5.5 0 016 3.1C5.4 4.2 5 5.6 4.9 7.2zm3.8 1.6h3.2c-.1 1.8-.7 3.5-1.6 4.7-.9-1.2-1.5-2.9-1.6-4.7zm4.7 0h2.3A5.5 5.5 0 0110 12.9c.6-1.1 1-2.5 1.1-4.1zm0-1.6c-.1-1.6-.5-3-1.1-4.1a5.5 5.5 0 013.4 4.1z"/></svg>www.harborledger-example.net</li>
    </ul>

    <svg class="footer-bands" viewBox="0 0 560 50" aria-hidden="true">
      <polygon points="0,34 284,28 262,50 0,50" fill="var(--grey)"/>
      <polygon points="274,50 298,22 560,6 560,50" fill="var(--slate)"/>
    </svg>
  </section>

  <section class="card card-back">
    <p class="back-name">Harbor Ledger</p>
    <p class="back-url">www.harborledger-example.net</p>
  </section>
</body>
</html>
```